Corvel Capital LLC

Need Professional Business cards for New Investment Fund

Target Market(s)

High Quality investors

Industry/Entity Type

Financial

Contact Information for Business Card

Phone Number +1 555 284 6190
Name Lukas Varenko
Title Fund Manager
email lv@FundKestovan.com
Website www.FundKestovan.com

Colors

Designer to choose colors to be used in the design.

Requirements
Must have
• Must have our Logo and all of the above. Must be made so lettering and loge can be raised

```html
<!DOCTYPE html>
<html lang="en">
<head>
<meta charset="utf-8">
<title>Kestovan Capital LLC — Business Card</title>
<link href="https://fonts.googleapis.com/css2?family=Questrial&display=swap" rel="stylesheet">
<style>
  :root {
    --backdrop: #1c1c1d;
    --card: #38383a;
    --edge-green: #2ee81c;
    --accent-green: #27e01a;
    --silver: #b9b9bb;
    --white: #f4f4f4;
    --rule: #8a8a8c;
  }
  * { margin: 0; padding: 0; box-sizing: border-box; }
  html, body {
    width: 1200px; height: 960px; overflow: hidden;
    background: var(--backdrop);
    font-family: "Questrial", "Century Gothic", sans-serif;
  }
  .sheet {
    width: 1200px; height: 960px;
    display: flex; flex-direction: column;
    align-items: center; justify-content: center; gap: 56px;
  }
  .card {
    position: relative;
    width: 700px; height: 400px;
    background: var(--card);
    border-bottom: 4px solid var(--edge-green);
    border-left: 2px solid var(--edge-green);
    box-shadow: 0 10px 30px rgba(0,0,0,0.5);
  }
  .card-front { display: flex; align-items: center; justify-content: center; }
  .wordmark-front {
    color: var(--silver);
    font-size: 52px;
    letter-spacing: 6px;
    white-space: nowrap;
  }
  .card-back { display: flex; align-items: center; padding-left: 90px; }
  .wordmark-back {
    width: 250px;
    display: flex; align-items: center; gap: 12px;
    color: var(--white);
    font-size: 34px;
    letter-spacing: 2px;
    white-space: nowrap;
  }
  .wordmark-dot { width: 16px; height: 16px; background: var(--accent-green); flex: none; }
  .divider {
    width: 1px; height: 140px; background: var(--rule);
    margin: 0 32px 0 12px; flex: none;
  }
  .details { color: var(--white); white-space: nowrap; }
  .holder-name { color: var(--accent-green); font-size: 26px; line-height: 1.1; }
  .holder-title { font-size: 16px; margin-bottom: 18px; }
  .contact-list { list-style: none; font-size: 14px; line-height: 1.6; }
  .contact-list li { display: flex; align-items: center; gap: 10px; }
  .contact-list svg { width: 13px; height: 13px; fill: var(--accent-green); flex: none; }
</style>
</head>
<body>
<main class="sheet">
  <section class="card card-front" aria-label="Card front">
    <div class="wordmark-front">Kestovan</div>
  </section>

  <section class="card card-back" aria-label="Card back">
    <div class="wordmark-back"><span class="wordmark-dot"></span>Kestovan</div>
    <div class="divider"></div>
    <div class="details">
      <p class="holder-name">Lukas Varenko</p>
      <p class="holder-title">Fund Manager</p>
      <ul class="contact-list">
        <li>
          <svg viewBox="0 0 24 24" aria-hidden="true"><path d="M6.6 10.8a15.1 15.1 0 0 0 6.6 6.6l2.2-2.2a1 1 0 0 1 1-.25 11.4 11.4 0 0 0 3.6.57 1 1 0 0 1 1 1V20a1 1 0 0 1-1 1A17 17 0 0 1 3 4a1 1 0 0 1 1-1h3.5a1 1 0 0 1 1 1c0 1.25.2 2.45.57 3.57a1 1 0 0 1-.25 1z"/></svg>
          +1 555 284 6190
        </li>
        <li>
          <svg viewBox="0 0 24 24" aria-hidden="true"><path d="M2 5h20v14H2z M2 5l10 8 10-8"/></svg>
          lv@FundKestovan.com
        </li>
        <li>
          <svg viewBox="0 0 24 24" aria-hidden="true"><circle cx="12" cy="12" r="10"/></svg>
          www.FundKestovan.com
        </li>
      </ul>
    </div>
  </section>
</main>
</body>
</html>
```